Silver Bloom Marisol's Cleaning Service Business Cards Project

A business card with all contact details with logo design on there (already have a logo) eye catching Logo and contact info on one side, full logo on the back, must target upper class residential and corporate companies, fitness companies, still keep it on the feminine side of things , must look elegant

Target Market(s)

Upper class homes and corporate companies

Industry/Entity Type

Cleaning Service

Contact Information for Business Card

Name: Marisol Quenby
Position: Director
ABN: 31647209853
Email: marisolssilvercleaning@tidymail.example
Number: 0417906354

Font styles to use
Decorative

Colors

Designer to choose colors to be used in the design.

Requirements
Must have
• Available Sydney Wide, contact info and logo on one side, full logo on the back
Nice to have
• Professional appearance
Should not have
• Cheap advert looking stuff

```html
<!DOCTYPE html>
<html lang="en">
<head>
<meta charset="utf-8">
<title>Silver Bloom – Business Cards</title>
<link rel="stylesheet" href="https://fonts.googleapis.com/css2?family=Cinzel:wght@500&family=Open+Sans:wght@400;600&family=Roboto+Condensed:wght@700&display=swap">
<style>
  :root {
    --page: #e9e6e1;
    --ink: #19191b;
    --teal: #2ee6dc;
    --aqua: #8ffcf8;
    --slate: #555a5e;
    --white: #ffffff;
    --ornament-dark: #1f5956;
    --ornament-light: #7ff1eb;
  }
  * { box-sizing: border-box; margin: 0; padding: 0; }
  html, body { width: 1200px; height: 960px; overflow: hidden; }
  body { background: var(--page); position: relative; font-family: "Open Sans", sans-serif; }

  .card { position: absolute; width: 600px; height: 342px; overflow: hidden; }
  .card-front { left: 314px; top: 113px; background: var(--ink); }
  .card-back { left: 311px; top: 472px; background: var(--teal); }

  .brand { position: absolute; left: 0; width: 600px; text-align: center; }
  .brand-name {
    top: 128px; font-family: "Cinzel", serif; font-weight: 500;
    font-size: 21px; letter-spacing: 1px; color: var(--teal);
  }
  .brand-tagline {
    top: 154px; font-size: 7.5px; font-weight: 600; letter-spacing: 2.4px;
    color: var(--white); text-transform: uppercase;
  }
  .ornament-front {
    position: absolute; left: 208px; top: 88px; width: 190px; height: 36px;
    background: linear-gradient(90deg, transparent, var(--ornament-dark) 20%, var(--ornament-dark) 80%, transparent);
    border-radius: 18px;
  }

  .panel { position: absolute; top: 192px; height: 107px; }
  .panel-name { left: 0; width: 296px; background: var(--teal); }
  .panel-contact { left: 307px; width: 293px; background: var(--aqua); overflow: hidden; }

  .person-name, .person-role {
    position: absolute; right: 39px; font-family: "Roboto Condensed", sans-serif;
    font-weight: 700; color: var(--slate); text-transform: uppercase;
  }
  .person-name { top: 32px; font-size: 21px; }
  .person-role { top: 57px; font-size: 14px; }

  .contact-list {
    position: absolute; left: 16px; right: 12px; top: 14px; list-style: none;
    color: var(--slate); font-size: 13.5px;
  }
  .contact-list li { display: flex; align-items: center; height: 20.5px; white-space: nowrap; }
  .contact-list svg { width: 12px; height: 12px; margin-right: 8px; fill: var(--slate); flex: none; }
  .contact-list .contact-email { font-size: 11.2px; letter-spacing: -0.1px; }

  .back-tagline, .back-web { position: absolute; left: 56px; color: var(--white); }
  .back-tagline { top: 117px; font-size: 10px; letter-spacing: 3.6px; text-transform: uppercase; }
  .back-web { top: 133px; font-size: 14.5px; letter-spacing: 3.4px; }

  .back-mark {
    position: absolute; left: 372px; top: 14px; width: 196px; height: 196px;
    border: 4px solid var(--white); border-radius: 50%;
    display: flex; align-items: center; justify-content: center;
  }
  .back-mark-name {
    font-family: "Cinzel", serif; font-weight: 500; font-size: 22px;
    color: var(--white); letter-spacing: 1px;
  }
  .ornament-back {
    position: absolute; left: 174px; top: 208px; width: 426px; height: 122px;
    background: linear-gradient(90deg, transparent, var(--ornament-light) 25%, var(--ornament-light));
    border-radius: 60px 0 0 60px;
  }
</style>
</head>
<body>
  <section class="card card-front">
    <div class="ornament-front" role="img" aria-label="Decorative floral scroll flourish"></div>
    <div class="brand brand-name">Silver Bloom</div>
    <div class="brand brand-tagline">Marisol's Cleaning Services</div>

    <div class="panel panel-name">
      <div class="person-name">Marisol Quenby</div>
      <div class="person-role">Director</div>
    </div>

    <div class="panel panel-contact">
      <ul class="contact-list">
        <li class="contact-abn">ABN: 31647209853</li>
        <li class="contact-phone">
          <svg viewBox="0 0 24 24"><path d="M6.6 10.8a15.1 15.1 0 0 0 6.6 6.6l2.2-2.2a1 1 0 0 1 1-.25 11.4 11.4 0 0 0 3.6.6 1 1 0 0 1 1 1V20a1 1 0 0 1-1 1A17 17 0 0 1 3 4a1 1 0 0 1 1-1h3.5a1 1 0 0 1 1 1c0 1.25.2 2.45.6 3.6a1 1 0 0 1-.25 1z"/></svg>
          0417906354
        </li>
        <li class="contact-email">
          <svg viewBox="0 0 24 24"><path d="M2 5h20v14H2zm2 2v.5l8 5 8-5V7l-8 5z"/></svg>
          marisolssilvercleaning@tidymail.example
        </li>
        <li class="contact-web">
          <svg viewBox="0 0 24 24"><circle cx="12" cy="12" r="10"/></svg>
          www.silverbloom.example
        </li>
      </ul>
    </div>
  </section>

  <section class="card card-back">
    <div class="back-tagline">Marisol's Cleaning Services</div>
    <div class="back-web">www.silverbloom.example</div>
    <div class="back-mark"><span class="back-mark-name">Silver Bloom</span></div>
    <div class="ornament-back" role="img" aria-label="Large decorative floral scroll flourish"></div>
  </section>
</body>
</html>
```